BOLD & MINIMALIST DESIGN NEEDED

We want a very bold but minimalistic business card design that is impactful and utilizes both sides of the business card. Our current logo is included for your use.

We want bold fonts and good use of negative space. We don't want the logo to overpower the design.

Target Market(s)

Professionals who are building new commercial buildings.

Industry/Entity Type

Construction

Contact Information for Business Card

Name, Title, email, office phone, cell phone, website

Font styles to use
Serif
Sans Serif

Requirements
Must have
• Bold design!

```html
<!DOCTYPE html>
<html lang="en">
<head>
<meta charset="utf-8">
<title>Ridgeline Design + Build — Business Card</title>
<link rel="stylesheet" href="https://fonts.googleapis.com/css2?family=Montserrat:wght@300;400;500&family=Oswald:wght@500;700&display=swap">
<style>
  :root {
    --backdrop: #d3d3cf;
    --paper: #ffffff;
    --brand-green: #84c225;
    --deep-green: #6fa81c;
    --ink: #0e0e0e;
    --muted-ink: #2a2a2a;
  }
  * { box-sizing: border-box; margin: 0; padding: 0; }
  html, body {
    width: 1200px; height: 801px; overflow: hidden;
    background: var(--backdrop);
  }
  .stage {
    position: relative; width: 1200px; height: 801px;
    display: flex; align-items: center; justify-content: center; gap: 40px;
  }
  .card {
    position: relative; width: 540px; height: 309px;
    box-shadow: 0 10px 24px rgba(0,0,0,0.18);
    overflow: hidden;
  }

  /* Front side */
  .card-front { background: var(--paper); }
  .brand-lockup {
    position: absolute; left: 150px; top: 52px;
    display: flex; align-items: center; gap: 10px;
  }
  .brand-square { width: 22px; height: 22px; background: var(--brand-green); }
  .brand-name {
    font-family: "Oswald", sans-serif; font-weight: 700;
    font-size: 25px; letter-spacing: 0.5px; color: var(--ink);
    line-height: 1;
  }
  .identity {
    position: absolute; left: 58px; top: 150px; width: 190px; text-align: right;
  }
  .person-name {
    font-family: "Oswald", sans-serif; font-weight: 700;
    font-size: 30px; line-height: 1; color: var(--brand-green);
    text-transform: uppercase;
  }
  .person-title {
    font-family: "Montserrat", sans-serif; font-weight: 400;
    font-size: 13px; letter-spacing: 1px; color: var(--muted-ink);
    margin-top: 4px;
  }
  .divider {
    position: absolute; left: 264px; top: 146px; width: 1.5px; height: 62px;
    background: var(--brand-green);
  }
  .contact-list {
    position: absolute; left: 280px; top: 146px; list-style: none;
    font-family: "Montserrat", sans-serif; font-weight: 400;
    font-size: 13px; color: var(--ink); line-height: 21px;
  }
  .contact-list li { display: flex; align-items: center; gap: 7px; }
  .contact-list svg { width: 12px; height: 12px; flex: none; }
  .web-band {
    position: absolute; left: 0; right: 0; bottom: 16px; height: 34px;
    background: var(--ink);
    display: flex; align-items: center; padding-left: 150px;
  }
  .web-address {
    font-family: "Montserrat", sans-serif; font-weight: 500;
    font-size: 13px; letter-spacing: 1px; color: var(--paper);
  }
  .web-address .accent { color: var(--brand-green); }
  .band-cap {
    position: absolute; right: 0; bottom: 50px; width: 64px; height: 20px;
    background: var(--brand-green);
  }
  .band-tab {
    position: absolute; right: 64px; bottom: 16px; width: 30px; height: 34px;
    background: var(--ink);
  }

  /* Back side */
  .card-back { background: var(--brand-green); }
  .back-pattern {
    position: absolute; inset: 0;
    background: linear-gradient(160deg, var(--brand-green) 0%, var(--deep-green) 100%);
  }
  .back-brand {
    position: absolute; right: 34px; bottom: 44px;
    font-family: "Oswald", sans-serif; font-weight: 700;
    font-size: 18px; letter-spacing: 0.5px; color: var(--paper);
  }
</style>
</head>
<body>
  <main class="stage">
    <section class="card card-front" aria-label="Card front">
      <div class="brand-lockup">
        <span class="brand-square"></span>
        <span class="brand-name">RIDGELINE DESIGN + BUILD</span>
      </div>

      <div class="identity">
        <p class="person-name">Marcus Whitfield</p>
        <p class="person-title">OWNER</p>
      </div>
      <div class="divider"></div>

      <ul class="contact-list">
        <li>
          <svg viewBox="0 0 12 12" aria-hidden="true"><path d="M2.2 1h2l1 2.6-1.3 1a6 6 0 0 0 3.5 3.5l1-1.3 2.6 1v2a1 1 0 0 1-1 1A9.2 9.2 0 0 1 1.2 2a1 1 0 0 1 1-1z" fill="#84c225"/></svg>
          (555) 214-7380
        </li>
        <li>
          <svg viewBox="0 0 12 12" aria-hidden="true"><path d="M1 4.5C1 2.5 11 2.5 11 4.5v1H8.6V4.4H3.4v1.1H1z" fill="#84c225"/><rect x="2.5" y="6" width="7" height="4.5" rx="1" fill="#84c225"/><circle cx="6" cy="8.2" r="1.2" fill="#fff"/></svg>
          (555) 214-7381
        </li>
        <li>
          <svg viewBox="0 0 12 12" aria-hidden="true"><rect x="1" y="2.5" width="10" height="7" fill="none" stroke="#84c225" stroke-width="1.2"/><path d="M1 2.5l5 4 5-4" fill="none" stroke="#84c225" stroke-width="1.2"/></svg>
          ridgelinebuild@mail.com
        </li>
      </ul>

      <div class="band-cap"></div>
      <div class="web-band">
        <p class="web-address">www.<span class="accent">ridgelinebuild</span>.com</p>
      </div>
    </section>

    <section class="card card-back" aria-label="Card back">
      <div class="back-pattern" role="img" aria-label="Embossed repeating brand pattern in tonal green"></div>
      <p class="back-brand">RIDGELINE</p>
    </section>
  </main>
</body>
</html>
```